Local Flower Farm Needs Business Card Design

I need business cards designed for a flower farm based in Eudora, Kansas.
Business Info:
We are a local cut flower farm located in Eudora, Kansas, founded by Corinne Haldwick. What started as a passion for agriculture and search for more joy in daily life has blossomed into a small business dedicated to providing the community with beautiful, fresh, and sustainable flowers. We specialize in local, seasonal blooms, ensuring that every petal reflects the care and dedication we pour into our craft. Our mission is to deliver the highest quality flowers directly to our customers through local farmers markets and to florists who share our commitment to sustainability. Join us in celebrating the beauty of nature, one bloom at a time!
Contact Details:
Corinne Haldwick
Owner
Phone 913-555-0147
Facebook: Rosalind Thorpe Gardens
Instagram: @RosalindThorpeGardens
Website: RosalindThorpeGardens.example
Target Market(s)
Wholesale to Florists and Direct to Consumer via Farmers Market
Industry/Entity Type
Florist, Farm
Contact Information for Business Card
Name, Contact Info, Logo
Look and feel
Each slider illustrates characteristics of the customer's brand and the style your logo design should communicate.

```html
<!DOCTYPE html>
<html lang="en">
<head>
<meta charset="utf-8">
<title>Rosalind Thorpe Gardens – Business Card</title>
<link rel="stylesheet" href="https://fonts.googleapis.com/css2?family=Tinos:wght@400;700&display=swap">
<style>
  :root {
    --stage: #3b3c3e;
    --ink: #0b262b;
    --paper: #ffffff;
    --paper-edge: #a9adb0;
    --text-light: #f2f4f4;
    --bloom-mid: #8a9a9c;
  }
  html, body {
    margin: 0;
    padding: 0;
    width: 1200px;
    height: 900px;
    overflow: hidden;
    background: var(--stage);
  }
  .stage {
    position: relative;
    width: 1200px;
    height: 900px;
  }
  .card {
    position: absolute;
    left: 250px;
    width: 700px;
    height: 400px;
    border-radius: 34px;
    overflow: hidden;
    box-shadow: 0 14px 30px rgba(0,0,0,0.45);
  }
  .card--front { top: 35px; }
  .card--back { top: 465px; }
  .card svg { display: block; }
  .brand-name {
    font-family: "Tinos", serif;
    font-weight: 400;
    fill: var(--ink);
    letter-spacing: 3px;
  }
  .contact-name {
    font-family: "Tinos", serif;
    font-weight: 700;
    fill: var(--text-light);
    font-size: 26px;
    letter-spacing: 1px;
  }
  .contact-role,
  .contact-line {
    font-family: "Tinos", serif;
    font-weight: 400;
    fill: var(--text-light);
  }
  .contact-role { font-size: 17px; }
  .contact-line { font-size: 19px; }
  .icon { fill: none; stroke: var(--text-light); stroke-width: 1.6; }
  .icon-dot { fill: var(--text-light); }
</style>
</head>
<body>
<main class="stage">

  <!-- Front of card -->
  <section class="card card--front">
    <svg width="700" height="400" viewBox="0 0 700 400">
      <defs>
        <radialGradient id="front-sheen" cx="50%" cy="45%" r="65%">
          <stop offset="0%" stop-color="var(--paper)"/>
          <stop offset="60%" stop-color="#eceeef"/>
          <stop offset="100%" stop-color="var(--paper-edge)"/>
        </radialGradient>
      </defs>
      <rect class="card-face" width="700" height="400" fill="url(#front-sheen)"/>
      <g class="brand-mark" transform="translate(350 200)">
        <circle r="112" fill="none" stroke="var(--ink)" stroke-width="1.5"/>
        <text class="brand-name" text-anchor="middle" y="-22" font-size="27">ROSALIND</text>
        <text class="brand-name" text-anchor="middle" y="12" font-size="27">THORPE</text>
        <text class="brand-name" text-anchor="middle" y="46" font-size="27">GARDENS</text>
      </g>
    </svg>
  </section>

  <!-- Back of card -->
  <section class="card card--back">
    <svg width="700" height="400" viewBox="0 0 700 400">
      <defs>
        <radialGradient id="bloom-glow" cx="50%" cy="50%" r="50%">
          <stop offset="0%" stop-color="var(--bloom-mid)" stop-opacity="0.45"/>
          <stop offset="100%" stop-color="var(--bloom-mid)" stop-opacity="0"/>
        </radialGradient>
      </defs>
      <rect class="card-face" width="700" height="400" fill="var(--paper)"/>
      <path class="ink-panel" d="M0 0 H300 C430 100 430 290 360 400 H0 Z" fill="var(--ink)"/>

      <ellipse class="floral-sprig" role="img" aria-label="Line drawing of a sprig of wildflowers and buds"
               cx="440" cy="135" rx="110" ry="115" fill="url(#bloom-glow)"/>

      <text class="contact-name" x="36" y="180">CORINNE HALDWICK</text>
      <text class="contact-role" x="62" y="205">Owner</text>

      <!-- phone -->
      <path class="icon" d="M44 241 q-2 6 4 12 q6 6 12 4 l2-4 -5-3 -2 2 q-4-2 -6-6 l2-2 -3-5 z"/>
      <text class="contact-line" x="72" y="256">913-555-0147</text>

      <!-- social page -->
      <circle class="icon-dot" cx="53" cy="278" r="8"/>
      <text class="contact-line" x="72" y="284">Rosalind Thorpe Gardens</text>

      <!-- social handle -->
      <circle class="icon-dot" cx="53" cy="306" r="8"/>
      <text class="contact-line" x="72" y="312">@RosalindThorpeGardens</text>

      <!-- website -->
      <g class="icon" transform="translate(53 334)">
        <circle r="8"/>
        <ellipse rx="3.5" ry="8"/>
        <line x1="-8" y1="0" x2="8" y2="0"/>
      </g>
      <text class="contact-line" x="72" y="340">RosalindThorpeGardens.example</text>

      <g class="brand-mark" transform="translate(570 195)">
        <circle r="100" fill="none" stroke="var(--ink)" stroke-width="1.4"/>
        <text class="brand-name" text-anchor="middle" y="-20" font-size="23">ROSALIND</text>
        <text class="brand-name" text-anchor="middle" y="10" font-size="23">THORPE</text>
        <text class="brand-name" text-anchor="middle" y="40" font-size="23">GARDENS</text>
      </g>
    </svg>
  </section>

</main>
</body>
</html>
```